Envelope design

We need a envelope design for a professional services firm called Brenwick Tax Advisory Inc. The firm is essentially a very specialized tax accounting firm - instead of serving the end consumer, we support other public accounting firms in the area of Canadian and U.S. tax advisory and compliance (i.e. they call us on tax issues too complex for the general practitioner). Our byline is "Tax Support Services for Public Accounting Firms". Our postcard should utilize our logo and be based on colours present in our logo (see file attached). The final design needs to convey professionalism and trustworthiness (we're hired by accountants after all!) while being creative and eye-catching. Eye-catching is critical, since many prospective recipients will not have heard from me before and I want them to read the postcard.
At lot of design work has already been done here. I've attached a number of sample files showing logo and letterhead designs. Please note that the letterhead hasn't yet been updated for the new logo. This is happening in a separate design competition.
Updates
Project Deadline Extended Reason: Deadline is extended because I am pricing the extra cost of having colour right to the edge of the envelopes. This will help me design on final design. Pricing should come in on Monday. Added Saturday, February 20, 2016

```html
<!DOCTYPE html>
<html lang="en">
<head>
<meta charset="utf-8">
<title>Brenwick Tax Advisory Inc. – Envelope</title>
<link href="https://fonts.googleapis.com/css2?family=Marcellus&family=Open+Sans:wght@400&family=Arimo&display=swap" rel="stylesheet">
<style>
  :root {
    --backdrop: #e9e6e1;
    --paper: #ffffff;
    --band: #161616;
    --ink: #222222;
    --label: #2b2b2b;
    --edge: #3a3a3a;
    --navy: #1f3f73;
    --orange: #ee7d22;
    --gold: #f4b63c;
  }
  * { box-sizing: border-box; margin: 0; padding: 0; }
  html, body { width: 1200px; height: 1000px; overflow: hidden; }
  body { background: var(--backdrop); position: relative; font-family: "Open Sans", sans-serif; }

  .view-label {
    position: absolute; left: 18px;
    font-family: "Arimo", Arial, sans-serif; font-size: 56px; line-height: 70px;
    color: var(--label);
  }
  .envelope {
    position: absolute; background: var(--paper);
    box-shadow: 0 2px 6px rgba(0,0,0,.25);
  }

  /* Front */
  .envelope--front { left: 287px; top: 10px; width: 653px; height: 284px; }
  .brand-band {
    height: 90px; background: var(--band);
    display: flex; align-items: center; justify-content: center; gap: 12px;
  }
  .brand-mark { width: 44px; height: 44px; background: var(--gold); flex: none; }
  .brand-text { color: #ffffff; font-family: "Marcellus", serif; text-transform: uppercase; }
  .brand-name { font-size: 27px; letter-spacing: 1px; line-height: 30px; }
  .brand-byline { font-size: 12.5px; letter-spacing: 3px; line-height: 16px; }

  /* Back, closed */
  .envelope--back-closed { left: 287px; top: 305px; width: 653px; height: 283px; }
  .flap-closed {
    position: absolute; left: 0; top: 0; width: 100%; height: 102px;
    border: 1px solid var(--edge); border-top: none;
    border-radius: 0 0 26px 26px;
  }

  /* Back, open */
  .envelope--back-open { left: 287px; top: 705px; width: 655px; height: 285px; }
  .flap-open {
    position: absolute; left: 287px; top: 604px; width: 655px; height: 101px;
    border-radius: 16px 16px 0 0;
    background: linear-gradient(90deg, var(--gold), var(--navy) 30%, var(--orange) 55%, var(--navy) 80%, var(--gold));
  }
  .liner {
    position: absolute; left: 8px; top: 0; width: 639px; height: 70px;
    border: 1px solid var(--edge); border-top: none;
    border-radius: 0 0 22px 22px;
    background: linear-gradient(90deg, var(--navy), var(--gold) 30%, var(--navy) 55%, var(--orange) 80%, var(--navy));
  }

  .return-address {
    position: absolute; left: 0; width: 100%;
    text-align: center; font-size: 7.6px; line-height: 13px; color: var(--ink);
  }
  .envelope--back-closed .return-address { top: 172px; }
  .envelope--back-open .return-address { top: 173px; }
  .sep { margin: 0 4px; }
</style>
</head>
<body>
  <div class="view-label" style="top:120px">Front</div>
  <div class="view-label" style="top:402px">Back -<br>Close</div>
  <div class="view-label" style="top:774px">Back -<br>Open</div>

  <section class="envelope envelope--front">
    <header class="brand-band">
      <span class="brand-mark"></span>
      <div class="brand-text">
        <div class="brand-name">Brenwick Tax Advisory</div>
        <div class="brand-byline">Tax Support for Public Accounting Firms</div>
      </div>
    </header>
  </section>

  <section class="envelope envelope--back-closed">
    <div class="flap-closed"></div>
    <address class="return-address" style="font-style:normal">
      18-410 Larchmere Road, Bedford, Nova Scotia, Canada B4A 2K7<br>
      T: 902.555.0142<span class="sep">|</span>F: 902.555.0187<span class="sep">|</span>E: owen@brenwicktax.example<br>
      www.brenwicktax.example
    </address>
  </section>

  <div class="flap-open" role="img" aria-label="Repeating brand pattern in gold, navy and orange on the open flap"></div>
  <section class="envelope envelope--back-open">
    <div class="liner" role="img" aria-label="Repeating brand pattern on the envelope liner"></div>
    <address class="return-address" style="font-style:normal">
      18-410 Larchmere Road, Bedford, Nova Scotia, Canada B4A 2K7<br>
      T: 902.555.0142<span class="sep">|</span>F: 902.555.0187<span class="sep">|</span>E: owen@brenwicktax.example<br>
      www.brenwicktax.example
    </address>
  </section>
</body>
</html>
```